DOUBLE SIDED BROCHURE NEEDED TO PROMOTE DOCTOR

I need a double sided DL size (99mm x 210mm) brochure, promoting a doctor seeing patients in a new area.

I want something professional. I have included the relevant information. I would also like the Dr's picture somwhere in the brochure, with a professional background. I wish to print these tomorrow, so i will pick a winner within 14 hours of posting this ad.

I have included an example of a brochures design that I recently saw, and its definietly a good starting point.

Industry/Entity Type

Medical

```html
<!DOCTYPE html>
<html lang="en">
<head>
<meta charset="utf-8">
<title>Dr. Elias Marlow – Referral Brochure</title>
<link href="https://fonts.googleapis.com/css2?family=Nunito:wght@400;600;700;800&display=swap" rel="stylesheet">
<style>
  :root{
    --teal:#38b2bd;
    --teal-deep:#2a929b;
    --teal-light:#8fd7dc;
    --aqua-pale:#d4f0f1;
    --ink:#1f3236;
    --ink-soft:#3d4b4e;
    --green-ink:#2f7f70;
    --grey-top:#eceeef;
    --grey-bottom:#c9cdcf;
    --charcoal:#4a5053;
    --white:#ffffff;
    --page:#eef1f2;
  }
  *{box-sizing:border-box;margin:0;padding:0}
  html,body{width:1200px;height:1192px;overflow:hidden;background:var(--page)}
  body{font-family:"Nunito",Arial,sans-serif;color:var(--ink);position:relative}
  .panel{position:absolute;top:87px;width:480px;height:1018px;overflow:hidden;background:var(--white);box-shadow:0 6px 18px rgba(0,0,0,.18)}
  .panel--front{left:80px}
  .panel--back{left:640px}
  .wave{position:absolute;left:0;width:100%;display:block}

  /* front */
  .front-header{position:absolute;left:0;top:0;width:100%;height:380px;background:linear-gradient(180deg,var(--teal) 0%,var(--teal-light) 55%,var(--aqua-pale) 100%)}
  .front-header__title{position:absolute;left:30px;top:24px;font-size:26px;font-weight:800;color:var(--white)}
  .front-header__body{position:absolute;left:30px;top:80px;width:420px;font-size:16px;line-height:1.38;color:var(--ink);font-weight:600}
  .front-header__body p+p{margin-top:18px}
  .front-header__body strong{font-weight:800}
  .clinic-photo{position:absolute;left:0;top:360px;width:100%;height:420px;background:linear-gradient(180deg,#5f9fd6 0%,#a9cfe8 35%,#d9c6a0 58%,#6f9a5a 85%,#4f7a45 100%)}
  .front-footer{position:absolute;left:0;top:770px;width:100%;height:248px;background:linear-gradient(180deg,var(--grey-top),var(--grey-bottom))}
  .front-footer__strip{position:absolute;left:0;bottom:0;width:100%;height:22px;background:var(--charcoal)}
  .contact-tab{position:absolute;left:0;top:42px;padding:9px 26px 9px 30px;background:var(--teal-deep);color:var(--white);font-weight:800;font-size:17px;border-radius:0 22px 22px 0;letter-spacing:.3px}
  .contact{position:absolute;left:30px;top:92px;font-size:15px;line-height:1.3;color:var(--ink)}
  .contact__label{color:var(--teal-deep);font-weight:800}
  .contact__row{display:flex;align-items:center;gap:6px}
  .contact__fax{color:var(--green-ink);font-weight:800}
  .icon{width:14px;height:14px;flex:none}
  .badge{position:absolute;right:18px;top:12px;width:160px;height:160px}
  .badge__text{position:absolute;inset:0;display:flex;flex-direction:column;align-items:center;justify-content:center;text-align:center;color:var(--ink);line-height:1.05}
  .badge__big{font-size:19px;font-weight:800;color:var(--white);letter-spacing:.5px}
  .badge__small{font-size:13px;font-weight:700;margin:3px 0}
  .badge__weeks{font-size:20px;font-weight:800}

  /* back */
  .back-header{position:absolute;left:0;top:0;width:100%;height:300px;background:linear-gradient(180deg,var(--teal) 0%,var(--teal-light) 60%,var(--aqua-pale) 100%)}
  .back-header__title{position:absolute;left:26px;top:22px;width:420px;font-size:24px;line-height:1.2;font-weight:800;color:var(--white)}
  .back-header__intro{position:absolute;left:26px;top:196px;width:410px;font-size:16px;line-height:1.38;font-weight:600;color:var(--ink)}
  .back-body{position:absolute;left:0;top:300px;width:100%;height:718px;background:linear-gradient(160deg,#f6f7f7 0%,#e1e4e5 100%)}
  .services{position:absolute;left:26px;list-style:none;font-size:16px;line-height:1.45;color:var(--ink-soft)}
  .services li{position:relative;padding-left:22px;margin-bottom:6px}
  .services li::before{content:"";position:absolute;left:2px;top:8px;width:8px;height:8px;border-radius:50%;background:var(--teal-deep)}
  .services--endocrine{top:360px}
  .services--general{top:620px}
  .services__note{display:block}
  .services__heading{position:absolute;left:26px;top:578px;font-size:19px;font-weight:800;color:var(--teal)}
  .back-footer{position:absolute;left:0;top:800px;width:100%;height:218px;background:linear-gradient(180deg,var(--teal) 0%,var(--teal-deep) 100%)}
  .back-contact{position:absolute;left:26px;top:866px;font-size:15px;line-height:1.3;color:var(--white)}
  .back-contact .contact__row{margin-top:2px}
  .back-contact__fax-note{font-size:11px;margin-top:14px}
  .doctor-photo{position:absolute;right:0;top:760px;width:200px;height:258px;background:linear-gradient(180deg,#cfd6d9 0%,#8e9aa0 45%,#2e3540 100%)}
</style>
</head>
<body>

<section class="panel panel--front" aria-label="Brochure front">
  <div class="front-header">
    <h1 class="front-header__title">Dear Doctors,</h1>
    <div class="front-header__body">
      <p>We are pleased to announce that <strong>Dr. Elias Marlow</strong> is now consulting in Harbourvale, seeing public and private patients.</p>
      <p>Guaranteed appointment within two weeks, with patients having the option of surgery at Westbrook Health Campus, Ashgrove General Hospital or St. Clare Private Bellmont.</p>
    </div>
  </div>

  <div class="clinic-photo" role="img" aria-label="Photo of the clinic entrance building with palm plants"></div>

  <svg class="wave" style="top:318px;height:70px" viewBox="0 0 480 70" preserveAspectRatio="none" aria-hidden="true">
    <path d="M0 30 C120 0 260 70 480 20 L480 70 L0 70Z" fill="#ffffff"/>
    <path d="M0 40 C130 12 270 78 480 30 L480 44 C280 88 130 30 0 56Z" fill="#2a929b"/>
  </svg>

  <div class="front-footer">
    <div class="contact-tab">CONTACT DETAILS:</div>
    <div class="contact">
      <div class="contact__row contact__label">
        <svg class="icon" viewBox="0 0 14 14"><path d="M7 1a4 4 0 0 0-4 4c0 3 4 8 4 8s4-5 4-8a4 4 0 0 0-4-4zm0 5.5A1.5 1.5 0 1 1 7 3.5a1.5 1.5 0 0 1 0 3z" fill="#1f3236"/></svg>
        Harbourvale Clinic:
      </div>
      <div>42 Linden Road</div>
      <div>Harbourvale WA 6999</div>
      <div class="contact__row contact__label">
        <svg class="icon" viewBox="0 0 14 14"><path d="M3 1h2l1 3-1.5 1a7 7 0 0 0 4.5 4.5L10 8l3 1v2a2 2 0 0 1-2 2C6 13 1 8 1 3a2 2 0 0 1 2-2z" fill="#1f3236"/></svg>
        Phone:
      </div>
      <div>1300 482 917</div>
      <div class="contact__row contact__fax">
        <svg class="icon" viewBox="0 0 14 14"><rect x="3" y="1" width="8" height="4" fill="#1f3236"/><rect x="1" y="5" width="12" height="6" rx="1" fill="#1f3236"/><rect x="3" y="9" width="8" height="4" fill="#ffffff" stroke="#1f3236"/></svg>
        Please send all referrals by fax to
      </div>
      <div class="contact__fax">(08) 5550 2143</div>
    </div>

    <div class="badge">
      <svg viewBox="0 0 160 160" width="160" height="160" aria-hidden="true">
        <g fill="#4fc0c8">
          <rect x="27" y="27" width="106" height="106" transform="rotate(0 80 80)"/>
          <rect x="27" y="27" width="106" height="106" transform="rotate(15 80 80)"/>
          <rect x="27" y="27" width="106" height="106" transform="rotate(30 80 80)"/>
          <rect x="27" y="27" width="106" height="106" transform="rotate(45 80 80)"/>
          <rect x="27" y="27" width="106" height="106" transform="rotate(60 80 80)"/>
          <rect x="27" y="27" width="106" height="106" transform="rotate(75 80 80)"/>
        </g>
        <circle cx="80" cy="80" r="64" fill="none" stroke="#ffffff" stroke-width="2" stroke-dasharray="3 3"/>
      </svg>
      <div class="badge__text">
        <span class="badge__big">GUARANTEED</span>
        <span class="badge__small">appointment within</span>
        <span class="badge__weeks">TWO WEEKS</span>
      </div>
    </div>
    <div class="front-footer__strip"></div>
  </div>

  <svg class="wave" style="top:735px;height:60px" viewBox="0 0 480 60" preserveAspectRatio="none" aria-hidden="true">
    <path d="M0 36 C140 60 300 0 480 22 L480 60 L0 60Z" fill="#eceeef"/>
    <path d="M0 26 C140 50 300 -8 480 12 L480 24 C300 4 140 62 0 40Z" fill="#38b2bd"/>
  </svg>
</section>

<section class="panel panel--back" aria-label="Brochure back">
  <div class="back-header">
    <h2 class="back-header__title">Dr. Elias Marlow is a highly trained specialised surgeon.</h2>
  </div>
  <svg class="wave" style="top:140px;height:50px" viewBox="0 0 480 50" preserveAspectRatio="none" aria-hidden="true">
    <path d="M0 20 C150 50 320 0 480 18 L480 28 C320 10 150 60 0 32Z" fill="#ffffff" opacity=".7"/>
  </svg>
  <p class="back-header__intro">in all areas of Endocrine, Breast and General Surgery. Including;</p>

  <div class="back-body"></div>
  <svg class="wave" style="top:272px;height:60px" viewBox="0 0 480 60" preserveAspectRatio="none" aria-hidden="true">
    <path d="M0 10 C160 50 320 0 480 24 L480 60 L0 60Z" fill="#f6f7f7"/>
    <path d="M0 6 C160 46 320 -4 480 18 L480 30 C320 8 160 58 0 20Z" fill="#2a929b"/>
  </svg>

  <ul class="services services--endocrine">
    <li>Thyroid Surgery</li>
    <li>Parathyroid surgery<span class="services__note">(including minimally invasive parathyroidectomy)</span></li>
    <li>Breast Cancer<span class="services__note">Benign breast lesions</span></li>
  </ul>

  <h3 class="services__heading">All areas of general surgery, such as:</h3>
  <ul class="services services--general">
    <li>Gallbladder surgery</li>
    <li>Hernia surgery</li>
    <li>Haemorrhoids</li>
    <li>Carpal Tunnel</li>
    <li>Vasectomy etc etc…</li>
  </ul>

  <div class="back-footer"></div>
  <svg class="wave" style="top:770px;height:60px" viewBox="0 0 480 60" preserveAspectRatio="none" aria-hidden="true">
    <path d="M0 40 C150 0 300 60 480 14 L480 60 L0 60Z" fill="#38b2bd"/>
    <path d="M0 30 C150 -10 300 50 480 4 L480 14 C300 60 150 0 0 40Z" fill="#8fd7dc"/>
  </svg>

  <div class="doctor-photo" role="img" aria-label="Portrait of Dr. Elias Marlow in a dark suit"></div>

  <div class="back-contact">
    <div>Harbourvale Clinic:</div>
    <div class="contact__row">
      <svg class="icon" viewBox="0 0 14 14"><path d="M7 1a4 4 0 0 0-4 4c0 3 4 8 4 8s4-5 4-8a4 4 0 0 0-4-4zm0 5.5A1.5 1.5 0 1 1 7 3.5a1.5 1.5 0 0 1 0 3z" fill="#ffffff"/></svg>
      42 Linden Road
    </div>
    <div>Harbourvale WA 6999</div>
    <div class="contact__row" style="margin-top:18px">
      <svg class="icon" viewBox="0 0 14 14"><path d="M3 1h2l1 3-1.5 1a7 7 0 0 0 4.5 4.5L10 8l3 1v2a2 2 0 0 1-2 2C6 13 1 8 1 3a2 2 0 0 1 2-2z" fill="#ffffff"/></svg>
      1300 482 917
    </div>
    <div class="back-contact__fax-note">Please send all referrals by fax to</div>
    <div class="contact__row">
      <svg class="icon" viewBox="0 0 14 14"><rect x="3" y="1" width="8" height="4" fill="#ffffff"/><rect x="1" y="5" width="12" height="6" rx="1" fill="#ffffff"/><rect x="3" y="9" width="8" height="4" fill="#2a929b" stroke="#ffffff"/></svg>
      (08) 5550 2143
    </div>
  </div>
</section>

</body>
</html>
```